Harborline Auto LLC

Car Dealer Customer Service
Address: 2874 Cresthaven Road, Shelbyville, TN 37162
web: www.harborlineautoxq.net
email: harborlineautoxq@mailnest.example
Phone: (931) 555-0148
Phone: (629) 555-0173

```html
<!DOCTYPE html>
<html lang="en">
<head>
<meta charset="utf-8">
<title>Harborline Auto – Business Card</title>
<link rel="stylesheet" href="https://fonts.googleapis.com/css2?family=Montserrat:wght@700&family=Poppins:wght@400;500&family=Oswald:wght@600&display=swap">
<style>
  :root {
    --bg: #2a2a2a;
    --card: #f1f1f1;
    --blue: #1f7bb0;
    --blue-deep: #1b6f9f;
    --gold: #e0a93a;
    --ink: #222222;
    --white: #ffffff;
  }
  * { margin: 0; padding: 0; box-sizing: border-box; }
  html, body { width: 1200px; height: 1138px; overflow: hidden; background: var(--bg); }
  .stage { position: relative; width: 1200px; height: 1138px; }

  .card {
    position: absolute;
    background: linear-gradient(135deg, #f7f7f7 0%, var(--card) 60%, #e9e9e9 100%);
    border-radius: 14px;
    overflow: hidden;
  }
  .card--front { left: 274px; top: 186px; width: 622px; height: 376px; }
  .card--back  { left: 276px; top: 608px; width: 618px; height: 374px; }

  .brand-mark {
    position: absolute; left: 50%; transform: translateX(-50%);
    width: 96px; height: 96px; border-radius: 50%;
    background: var(--gold);
  }
  .card--front .brand-mark { top: 96px; }
  .card--back .brand-mark { top: 62px; }

  .brand-name {
    position: absolute; left: 0; right: 0; text-align: center;
    font-family: "Montserrat", sans-serif; font-weight: 700;
    font-size: 31px; letter-spacing: 0.5px; color: var(--blue);
    text-transform: uppercase;
  }
  .card--front .brand-name { top: 218px; }
  .card--back .brand-name { top: 178px; }

  .front-web {
    position: absolute; left: 0; right: 0; top: 322px;
    display: flex; justify-content: center; align-items: center; gap: 24px;
    font-family: "Poppins", sans-serif; font-size: 14px; color: var(--ink);
  }
  .front-web .rule { width: 54px; height: 2px; background: var(--gold); }

  .front-band { position: absolute; left: 0; right: 0; bottom: 0; height: 18px; display: flex; }
  .front-band .half-blue { flex: 1; background: var(--blue); }
  .front-band .half-gold { flex: 1; background: var(--gold); }

  .tagline {
    position: absolute; left: 0; right: 0; top: 236px; text-align: center;
    font-family: "Poppins", sans-serif; font-size: 15px; color: var(--ink);
  }
  .phone-band {
    position: absolute; left: 0; right: 0; top: 260px; height: 44px;
    background: var(--blue-deep);
    display: flex; justify-content: center; align-items: center; gap: 16px;
  }
  .phone {
    display: flex; align-items: center; gap: 10px;
    font-family: "Oswald", sans-serif; font-weight: 600; font-size: 29px;
    color: var(--white); letter-spacing: 0.3px;
  }
  .phone svg { width: 26px; height: 26px; }
  .contact-lines {
    position: absolute; left: 0; right: 0; top: 314px; text-align: center;
    font-family: "Poppins", sans-serif; font-size: 14.5px; line-height: 21px; color: var(--ink);
  }
</style>
</head>
<body>
<main class="stage">

  <section class="card card--front">
    <div class="brand-mark"></div>
    <h1 class="brand-name">Harborline Auto</h1>
    <div class="front-web">
      <span class="rule"></span>
      <span>www.harborlineautoxq.net</span>
      <span class="rule"></span>
    </div>
    <div class="front-band"><span class="half-blue"></span><span class="half-gold"></span></div>
  </section>

  <section class="card card--back">
    <div class="brand-mark"></div>
    <h2 class="brand-name">Harborline Auto</h2>
    <p class="tagline">Car Dealer Customer Service</p>
    <div class="phone-band">
      <span class="phone">
        <svg viewBox="0 0 26 26" aria-hidden="true"><circle cx="13" cy="13" r="11.5" fill="none" stroke="#e0a93a" stroke-width="2"/><path d="M9 7.5l2 0 1 3-1.4 1.2a7 7 0 0 0 3.7 3.7L15.5 14l3 1v2a1.5 1.5 0 0 1-1.6 1.5A10 10 0 0 1 7.5 9.1 1.5 1.5 0 0 1 9 7.5z" fill="#e0a93a"/></svg>
        931-555-0148
      </span>
      <span class="phone">
        <svg viewBox="0 0 26 26" aria-hidden="true"><circle cx="13" cy="13" r="11.5" fill="none" stroke="#e0a93a" stroke-width="2"/><path d="M9 7.5l2 0 1 3-1.4 1.2a7 7 0 0 0 3.7 3.7L15.5 14l3 1v2a1.5 1.5 0 0 1-1.6 1.5A10 10 0 0 1 7.5 9.1 1.5 1.5 0 0 1 9 7.5z" fill="#e0a93a"/></svg>
        629-555-0173
      </span>
    </div>
    <div class="contact-lines">
      <p>2874 Cresthaven Road, Shelbyville, TN 37162</p>
      <p>www.harborlineautoxq.net &nbsp;|&nbsp; harborlineautoxq@mailnest.example</p>
    </div>
  </section>

</main>
</body>
</html>
```